BrimFalcon Business Cards

We have a defined brand. Please visit our website to get a feel for the product and the color pallets. www.brimfalcon-example.com

We need an updated, world class business card design. (See the attached existing card design). Please utilize BOTH sides of the card as shown and be creative with the layout. I do want the horse head icon to be positioned as it is with the existing card.

The remainder of the layout can be customized and I also want it vertically oriented.

Attached are the logo files and please use the colors as follows:
Green - #A5CE39
Tan - #CDBD99
Black

Feel free to play with the colors.

```html
<!DOCTYPE html>
<html lang="en">
<head>
<meta charset="utf-8">
<title>BrimFalcon Business Cards</title>
<link href="https://fonts.googleapis.com/css2?family=Open+Sans:wght@400;600;700&display=swap" rel="stylesheet">
<style>
  :root {
    --bg: #8a8a8a;
    --card: #ffffff;
    --ink: #111111;
    --green-deep: #3a8d46;
    --green-light: #c9d22a;
    --accent: #a5ce39;
  }
  * { margin: 0; padding: 0; box-sizing: border-box; }
  html, body { width: 1200px; height: 960px; overflow: hidden; }
  body {
    background: var(--bg);
    font-family: "Open Sans", Arial, sans-serif;
    display: flex;
    flex-direction: column;
    align-items: center;
    justify-content: center;
    gap: 56px;
  }
  .card {
    position: relative;
    width: 700px;
    height: 400px;
    background: var(--card);
    overflow: hidden;
    box-shadow: 0 10px 24px rgba(0,0,0,0.35);
  }
  .brand {
    position: absolute;
    display: flex;
    align-items: center;
    gap: 12px;
  }
  .brand-mark {
    width: 46px; height: 46px;
    border-radius: 50%;
    background: var(--ink);
    flex: none;
  }
  .brand-name {
    font-weight: 700;
    font-size: 40px;
    line-height: 1;
    color: var(--ink);
    letter-spacing: 0.5px;
  }
  .brand-tagline {
    font-weight: 600;
    font-size: 15px;
    letter-spacing: 4.5px;
    color: var(--ink);
    margin-top: 6px;
  }
  .card-front .brand { left: 195px; top: 160px; }
  .card-back .brand { left: 48px; top: 128px; }
  .card-back .wave { position: absolute; inset: 0; }
  .contact {
    position: absolute;
    right: 30px;
    top: 118px;
    text-align: right;
    font-size: 14px;
    color: var(--ink);
    line-height: 1.35;
  }
  .contact-address { margin-bottom: 10px; padding-right: 32px; }
  .contact-row {
    display: flex;
    justify-content: flex-end;
    align-items: center;
    gap: 10px;
    margin-top: 6px;
  }
  .contact-row svg { width: 20px; height: 20px; flex: none; }
</style>
</head>
<body>

<section class="card card-front" aria-label="Card front">
  <div class="brand">
    <span class="brand-mark"></span>
    <div>
      <div class="brand-name">BrimFalcon</div>
      <div class="brand-tagline">Electric Motion Works</div>
    </div>
  </div>
</section>

<section class="card card-back" aria-label="Card back">
  <svg class="wave" viewBox="0 0 700 400" aria-hidden="true">
    <defs>
      <radialGradient id="greenGlow" cx="520" cy="225" r="330" gradientUnits="userSpaceOnUse">
        <stop offset="0" stop-color="var(--green-light)"/>
        <stop offset="1" stop-color="var(--green-deep)"/>
      </radialGradient>
    </defs>
    <path d="M215 400 C330 380 360 300 410 210 C470 100 560 40 700 10 L700 400 Z" fill="url(#greenGlow)"/>
    <path d="M190 396 C300 392 330 300 380 210 C410 150 430 110 455 85" fill="none" stroke="var(--ink)" stroke-width="5" stroke-linecap="round"/>
    <path d="M478 170 C520 90 590 45 700 22 L700 34 C600 52 530 100 478 170 Z" fill="var(--card)"/>
  </svg>

  <div class="brand">
    <span class="brand-mark"></span>
    <div>
      <div class="brand-name">BrimFalcon</div>
      <div class="brand-tagline">Electric Motion Works</div>
    </div>
  </div>

  <div class="contact">
    <div class="contact-address">18 Harbor Lane Suite 200<br>Northfield MI 40100</div>
    <div class="contact-row">
      <span>555-010-4477</span>
      <svg viewBox="0 0 24 24" aria-label="Phone"><path d="M6.6 10.8a15 15 0 0 0 6.6 6.6l2.2-2.2c.3-.3.7-.4 1-.2 1.1.4 2.3.6 3.6.6.6 0 1 .4 1 1V20c0 .6-.4 1-1 1C10.6 21 3 13.4 3 4c0-.6.4-1 1-1h3.5c.6 0 1 .4 1 1 0 1.3.2 2.5.6 3.6.1.3 0 .7-.2 1z" fill="var(--ink)"/></svg>
    </div>
    <div class="contact-row">
      <span>555-010-4478</span>
      <svg viewBox="0 0 24 24" aria-label="Fax"><path d="M7 3h10v5H7zM4 9h16a1 1 0 0 1 1 1v7h-4v4H7v-4H3v-7a1 1 0 0 1 1-1zm5 6v4h6v-4z" fill="var(--ink)"/></svg>
    </div>
    <div class="contact-row">
      <span>alexmorgan@brimfalcon-example.com</span>
      <svg viewBox="0 0 24 24" aria-label="Email"><path d="M3 5h18v14H3z" fill="var(--ink)"/><path d="M3 5l9 8 9-8" fill="none" stroke="var(--card)" stroke-width="1.5"/></svg>
    </div>
  </div>
</section>

</body>
</html>
```